New Innovative Counselling and psychotherapy Service needs Business Card design

Keep it simple and professional. On one side, just company name and logo (perhaps in all blue) and maybe a tag line.

On other side (all white) my name and Qualifications in centre

Industry/Entity Type

Health And Wellness

Contact Information for Business Card

Dara Whelby
Counsellor & Psychotherapist
BSc (Psychol.), BA, Dip. (Couns. & Psych.), PG.Cert (CBT), FGTrK, ONRE

I will also require Mobile no, Email and web site address of which I'll pass on to final designer.

Font styles to use
Sans Serif

Requirements
Must have
• My Logo Only and please use the colours in logo that is in it.
Should not have
• Any other images

```html
<!DOCTYPE html>
<html lang="en">
<head>
<meta charset="utf-8">
<title>Kestrel Path – Business Card</title>
<link rel="stylesheet" href="https://fonts.googleapis.com/css2?family=Open+Sans:wght@400;600;700&display=swap">
<style>
  :root {
    --stage: #2b2b2d;
    --sky-light: #6edcf7;
    --sky: #41b1ec;
    --sky-deep: #3aa6e6;
    --paper: #f4f5f6;
    --ink: #4a4f55;
    --tagline: #4d6472;
    --white: #ffffff;
  }
  * { margin: 0; padding: 0; box-sizing: border-box; }
  html, body {
    width: 1200px; height: 900px; overflow: hidden;
    background: var(--stage);
    font-family: "Open Sans", Arial, sans-serif;
  }
  .stage {
    position: relative; width: 1200px; height: 900px;
    display: flex; flex-direction: column; align-items: center; justify-content: center; gap: 52px;
  }
  .card {
    position: relative; width: 630px; height: 360px; overflow: hidden;
    box-shadow: 0 10px 30px rgba(0,0,0,.45);
  }
  /* Front */
  .card--front {
    background: linear-gradient(100deg, var(--sky-light) 0%, var(--sky) 55%, var(--sky-deep) 100%);
  }
  .front-mark {
    position: absolute; left: 50%; top: 62px; transform: translateX(-50%);
    display: flex; flex-direction: column; align-items: center; gap: 16px;
  }
  .front-mark__dot {
    width: 96px; height: 96px; border-radius: 50%; background: var(--white);
  }
  .front-mark__name {
    font-weight: 600; font-size: 26px; color: var(--white); letter-spacing: .5px;
  }
  .tagline {
    position: absolute; left: 0; right: 0; bottom: 36px; text-align: center;
    font-size: 15px; color: var(--tagline); letter-spacing: .2px;
  }
  /* Back */
  .card--back { background: var(--paper); }
  .brand {
    position: absolute; left: 44px; top: 196px;
    display: flex; align-items: center; gap: 14px;
  }
  .brand__dot { width: 40px; height: 40px; border-radius: 50%; background: var(--sky); }
  .brand__name { font-size: 25px; font-weight: 400; color: var(--ink); letter-spacing: .3px; }
  .details {
    position: absolute; left: 322px; right: 0; top: 44px; height: 214px;
    background: var(--sky); color: var(--white);
    padding: 22px 22px 0 28px;
  }
  .details__name { font-size: 19px; font-weight: 700; text-transform: uppercase; line-height: 1.1; }
  .details__role { font-size: 14.5px; font-weight: 400; text-transform: uppercase; letter-spacing: .3px; margin-top: 2px; }
  .details__quals { font-size: 10.5px; line-height: 1.35; margin-top: 4px; }
  .contact { list-style: none; margin-top: 10px; }
  .contact li { display: flex; align-items: center; gap: 10px; font-size: 13.5px; line-height: 1.45; }
  .contact svg { width: 13px; height: 13px; flex: none; }
</style>
</head>
<body>
<main class="stage">
  <section class="card card--front" aria-label="Card front">
    <div class="front-mark">
      <span class="front-mark__dot"></span>
      <span class="front-mark__name">Kestrel Path</span>
    </div>
    <p class="tagline">Caring For Your Psychological Well-Being Is Our Top Priority</p>
  </section>

  <section class="card card--back" aria-label="Card back">
    <div class="brand">
      <span class="brand__dot"></span>
      <span class="brand__name">Kestrel Path</span>
    </div>
    <div class="details">
      <h1 class="details__name">Dara Whelby</h1>
      <p class="details__role">Counsellor &amp; Psychotherapist</p>
      <p class="details__quals">BSc (Psychol.), BA, Dip. (Couns. &amp; Psych.)<br>PG.Cert (CBT), FGTrK,</p>
      <ul class="contact">
        <li>
          <svg viewBox="0 0 14 14" aria-hidden="true"><rect x="3.5" y="0.5" width="7" height="13" rx="1.2" fill="none" stroke="#fff" stroke-width="1.4"/><rect x="5.5" y="10.8" width="3" height="1.1" fill="#fff"/></svg>
          555 204 7180
        </li>
        <li>
          <svg viewBox="0 0 14 14" aria-hidden="true"><rect x="0.5" y="2.5" width="13" height="9" fill="#fff"/><path d="M0.8 3 L7 8 L13.2 3" fill="none" stroke="#41b1ec" stroke-width="1.2"/></svg>
          dara@kestrelpath.com
        </li>
        <li>
          <svg viewBox="0 0 14 14" aria-hidden="true"><circle cx="7" cy="7" r="6" fill="#fff"/><ellipse cx="7" cy="7" rx="2.6" ry="6" fill="none" stroke="#41b1ec" stroke-width="1"/><line x1="1" y1="7" x2="13" y2="7" stroke="#41b1ec" stroke-width="1"/></svg>
          www.kestrelpath.com
        </li>
      </ul>
    </div>
  </section>
</main>
</body>
</html>
```